Business Card Design

Just looking for a good designs that looks good with our company logo. I'd like it to be simple and to the point. Just including contact information, our logo, and my name somewhere on the card so future clients know who they're contacting, and a couple services offered. The two images I attached are pictures of our logo. I don't care which color they they are, I just attached both images to give a reference of logo colors depending on the color of the card.
Names: Carl Whitby
Phone: 816-555-0147
Email: greenstripeyard@fernmail.test
Services offered:
Mowing
Fertilization
Aeration
Bed & tree maintenance
and more.
Business
Names: Carl Whitby
Phone: 816-555-0147
(no website)

```html
<!DOCTYPE html>
<html lang="en">
<head>
<meta charset="utf-8">
<title>Greenstripe Yard – Business Card</title>
<link rel="stylesheet" href="https://fonts.googleapis.com/css2?family=Questrial&display=swap">
<style>
  :root {
    --paper: #ffffff;
    --ink: #111111;
    --navy: #1c2a45;
    --accent: #e3151b;
    --accent-soft: #f6a3a5;
  }
  * { margin: 0; padding: 0; box-sizing: border-box; }
  html, body {
    width: 1200px;
    height: 694px;
    overflow: hidden;
    background: var(--paper);
  }
  .card {
    position: relative;
    width: 1200px;
    height: 694px;
    background: var(--paper);
    font-family: "Questrial", sans-serif;
    color: var(--ink);
  }
  .brand {
    position: absolute;
    left: 196px;
    top: 188px;
    width: 280px;
    display: flex;
    align-items: center;
    gap: 18px;
  }
  .brand-dot {
    flex: none;
    width: 58px;
    height: 58px;
    border-radius: 50%;
    background: var(--accent);
  }
  .brand-name {
    font-size: 40px;
    line-height: 1.05;
    color: var(--navy);
  }
  .contact {
    position: absolute;
    left: 56px;
    top: 372px;
    width: 560px;
    text-align: center;
  }
  .contact-name {
    font-size: 46px;
    letter-spacing: 5px;
    line-height: 1;
  }
  .contact-phone {
    margin-top: 26px;
    font-size: 28px;
    letter-spacing: 4px;
    line-height: 1;
  }
  .contact-email {
    margin-top: 12px;
    font-size: 31px;
    letter-spacing: 0.5px;
    line-height: 1;
  }
  .services {
    position: absolute;
    left: 624px;
    top: 146px;
  }
  .services-title {
    font-size: 42px;
    font-weight: 400;
    line-height: 1;
    margin-bottom: 33px;
  }
  .service-list { list-style: none; }
  .service-item {
    display: flex;
    align-items: center;
    height: 74.5px;
    font-size: 37px;
    line-height: 1;
  }
  .service-bullet {
    flex: none;
    width: 26px;
    height: 26px;
    margin-left: 4px;
    margin-right: 28px;
  }
</style>
</head>
<body>
  <main class="card">
    <div class="brand">
      <span class="brand-dot"></span>
      <span class="brand-name">Greenstripe<br>Yard</span>
    </div>

    <section class="contact">
      <p class="contact-name">Carl Whitby</p>
      <p class="contact-phone">816-555-0147</p>
      <p class="contact-email">greenstripeyard@fernmail.test</p>
    </section>

    <section class="services">
      <h2 class="services-title">Services Offered</h2>
      <ul class="service-list">
        <li class="service-item"><svg class="service-bullet" viewBox="0 0 26 26" aria-hidden="true"><circle cx="13" cy="13" r="11.5" fill="none" stroke="var(--accent-soft)" stroke-width="3"/><circle cx="13" cy="13" r="8" fill="var(--accent)"/></svg>Mowing</li>
        <li class="service-item"><svg class="service-bullet" viewBox="0 0 26 26" aria-hidden="true"><circle cx="13" cy="13" r="11.5" fill="none" stroke="var(--accent-soft)" stroke-width="3"/><circle cx="13" cy="13" r="8" fill="var(--accent)"/></svg>Fertilization</li>
        <li class="service-item"><svg class="service-bullet" viewBox="0 0 26 26" aria-hidden="true"><circle cx="13" cy="13" r="11.5" fill="none" stroke="var(--accent-soft)" stroke-width="3"/><circle cx="13" cy="13" r="8" fill="var(--accent)"/></svg>Aeration</li>
        <li class="service-item"><svg class="service-bullet" viewBox="0 0 26 26" aria-hidden="true"><circle cx="13" cy="13" r="11.5" fill="none" stroke="var(--accent-soft)" stroke-width="3"/><circle cx="13" cy="13" r="8" fill="var(--accent)"/></svg>Bed &amp; tree maintenance</li>
        <li class="service-item"><svg class="service-bullet" viewBox="0 0 26 26" aria-hidden="true"><circle cx="13" cy="13" r="11.5" fill="none" stroke="var(--accent-soft)" stroke-width="3"/><circle cx="13" cy="13" r="8" fill="var(--accent)"/></svg>and more.</li>
      </ul>
    </section>
  </main>
</body>
</html>
```